Financial Advisor Resource Firm needs business card design

Need business card design for company in Omaha NE called Meridale Circle. We provide resources to financial advisors....workshop programs, retirement analysis, and insurance planning. I would like to see designs that use grays, greens, black, and white colors. The final design should communicate 'collaboration' and be simple yet attractive to financial planning clients. I will attached our logo and another picture of a puzzle piece coming together. I would like the incorporate the puzzle picture somehow, maybe on the back somehow, with color or just the gray scale....OR, the picture be the front of the card with 'Meridale' definition on it (see upload) and then company logo, employee name, title, address on the back (see ppt uploaded). The following disclosure needs to be included somewhere- Advisory services offered through Stonebrook Assets, LLC.
Updates

I uploaded a svg and ai file of the logo

Target Market(s)

Financial planning clients and financial advisors....so pretty diverse age range of about 40-70.

Industry/Entity Type

Financial Planning

Contact Information for Business Card

Tobias L. Fenwright, MBA
Founder/President
5287 E. Larkin Road
Suite 230
Omaha, NE 68190
Phone- (402) 555-0147
Cell- (402) 555-0183
Fax- (402) 555-0129
email- tobias@meridaleplan.example
web address- www.meridaleplan.example

Colors
1b1b1b
474747
d3d3d3
ffffff
9bcb3c
abd036

Requirements
Must have
• Must include logo provided, must be 2 sided, and must have disclosure...all of these items listed in project description

```html
<!DOCTYPE html>
<html lang="en">
<head>
<meta charset="utf-8">
<title>Meridale Circle – Business Card</title>
<link rel="stylesheet" href="https://fonts.googleapis.com/css2?family=Source+Sans+3:wght@400;600&family=Montserrat:wght@400&display=swap">
<style>
  :root {
    --ink: #1b1b1b;
    --charcoal: #474747;
    --mist: #d3d3d3;
    --white: #ffffff;
    --green: #8dc14f;
    --stage-light: #e6e7e9;
    --stage-dark: #cfd0d2;
  }
  * { box-sizing: border-box; margin: 0; padding: 0; }
  html, body { width: 800px; height: 1200px; overflow: hidden; }
  body {
    position: relative;
    background: radial-gradient(ellipse at 50% 50%, var(--stage-light) 0%, var(--stage-dark) 80%);
    font-family: "Source Sans 3", Arial, sans-serif;
  }
  .card {
    position: absolute;
    left: 148px;
    width: 504px;
    height: 288px;
    overflow: hidden;
  }
  .card--front { top: 170px; background: var(--white); }
  .card--back { top: 703px; }

  .brand {
    position: absolute;
    display: flex;
    align-items: center;
    gap: 10px;
    font-weight: 600;
    font-size: 36px;
    letter-spacing: 0.5px;
    white-space: nowrap;
  }
  .brand__dot { width: 14px; height: 14px; border-radius: 50%; background: var(--green); flex: none; }
  .card--front .brand { left: 0; right: 0; top: 52px; justify-content: center; color: var(--ink); }

  .person { position: absolute; right: 255px; top: 162px; text-align: right; }
  .person__name { color: var(--green); font-weight: 600; font-size: 20px; line-height: 24px; white-space: nowrap; }
  .person__title { color: var(--charcoal); font-size: 13px; line-height: 18px; margin-top: 2px; }

  .divider { position: absolute; left: 262px; top: 142px; width: 1px; height: 84px; background: var(--charcoal); }

  .contacts { position: absolute; left: 277px; top: 141px; list-style: none; }
  .contacts li {
    display: flex; align-items: center; gap: 5px;
    color: var(--charcoal); font-size: 13px; line-height: 16.8px; white-space: nowrap;
  }
  .contacts svg { width: 10px; height: 10px; fill: var(--green); flex: none; }

  .rule { position: absolute; left: 0; width: 100%; height: 3px; background: var(--ink); }
  .rule--top { top: 241px; }
  .rule--bottom { top: 286px; }
  .address-band {
    position: absolute; left: 0; top: 247px; width: 100%; height: 35px;
    background: var(--green); color: var(--white);
    font-size: 12.5px; line-height: 35px; text-align: center;
  }

  .back-photo {
    position: absolute; inset: 0;
    background:
      radial-gradient(ellipse at 20% 20%, #b9b9b9 0%, rgba(185,185,185,0) 50%),
      linear-gradient(160deg, #8e8e8e 0%, #6a6a6a 45%, #3f3f3f 100%);
  }
  .card--back .brand { left: 0; right: 0; top: 106px; justify-content: center; color: var(--white); }
  .tagline {
    position: absolute; left: 0; right: 0; top: 198px;
    text-align: center; color: var(--white);
    font-family: "Montserrat", Arial, sans-serif; font-size: 11.5px; letter-spacing: 0.1px;
  }
  .disclosure {
    position: absolute; left: 0; right: 0; bottom: 12px;
    text-align: center; color: var(--mist);
    font-size: 9px; letter-spacing: 0.2px;
  }
</style>
</head>
<body>

<section class="card card--front" aria-label="Card front">
  <div class="brand"><span class="brand__dot"></span>Meridale Circle</div>

  <div class="person">
    <p class="person__name">Tobias L. Fenwright, MBA</p>
    <p class="person__title">Founder/President</p>
  </div>

  <div class="divider"></div>

  <ul class="contacts">
    <li><svg viewBox="0 0 10 10"><path d="M2 0.5 L4 2.8 L3 4 Q4 6 6 7 L7.2 6 L9.5 8 L8 9.5 Q4 9.5 0.5 2 Z"/></svg>(402) 555-0147</li>
    <li><svg viewBox="0 0 10 10"><path d="M2.5 0 H7.5 V10 H2.5 Z M3.3 1 V8 H6.7 V1 Z"/></svg>(402) 555-0183</li>
    <li><svg viewBox="0 0 10 10"><path d="M2.5 0 H7.5 V3 H9.5 V9 H0.5 V3 H2.5 Z M3.3 0.8 V3 H6.7 V0.8 Z M2 5 V6 H8 V5 Z"/></svg>(402) 555-0129</li>
    <li><svg viewBox="0 0 10 10"><path d="M0.5 2 H9.5 V8.5 H0.5 Z M1.3 2.8 L5 5.6 L8.7 2.8 Z"/></svg>tobias@meridaleplan.example</li>
    <li><svg viewBox="0 0 10 10"><path d="M5 0.5 A4.5 4.5 0 1 0 5 9.5 A4.5 4.5 0 1 0 5 0.5 Z M1.5 4.5 H8.5 V5.5 H1.5 Z M4.5 1 H5.5 V9 H4.5 Z" fill-rule="evenodd"/></svg>www.meridaleplan.example</li>
  </ul>

  <div class="rule rule--top"></div>
  <p class="address-band">5287 E. Larkin Road Suite 230 Omaha, NE 68190</p>
  <div class="rule rule--bottom"></div>
</section>

<section class="card card--back" aria-label="Card back">
  <div class="back-photo" role="img" aria-label="Grayscale photo of several hands fitting puzzle pieces together"></div>
  <div class="brand"><span class="brand__dot"></span>Meridale Circle</div>
  <p class="tagline">TO COME TOGETHER AND UNITE IN COMMON INTEREST AND FOCUS</p>
  <p class="disclosure">Advisory services offered through Stonebrook Assets, LLC.</p>
</section>

</body>
</html>
```